Letter and Envelope Design For Harborline Realty

Please design a letter and an envelope incorporating our logo (See Attached). We are also launched a business card contest. Since we want them to match, please feel free to submit a design for both the business card and also the letter design and envelope.

Requirements
Must have
• The envelope, the letter and the business cards must match somehow connecting the designs. We want them to have something that holds them together besides the logo.

```html
<!DOCTYPE html>
<html lang="en">
<head>
<meta charset="utf-8">
<title>Harborline Realty Stationery</title>
<link href="https://fonts.googleapis.com/css2?family=Open+Sans:wght@400;600&display=swap" rel="stylesheet">
<style>
  :root{
    --ink:#1e1e1e;
    --text:#444444;
    --slate:#5a5a5a;
    --paper:#ffffff;
    --stage:#ececec;
    --rule:#8a8a8a;
  }
  *{margin:0;padding:0;box-sizing:border-box}
  html,body{width:1200px;height:1200px;overflow:hidden;background:var(--stage)}
  body{position:relative;font-family:"Open Sans",sans-serif;color:var(--text)}
  .sprite{position:absolute;width:0;height:0}
  .piece{position:absolute;background:var(--paper);overflow:hidden}
  .abs{position:absolute}

  /* brand lockup */
  .brand{position:absolute;display:flex;flex-direction:column;align-items:center}
  .brand-ring{border:3px solid var(--ink);border-radius:50%}
  .brand-name{font-weight:600;color:var(--ink);letter-spacing:.12em;text-align:center;line-height:1.2;text-transform:uppercase}

  /* contact list */
  .contact{position:absolute;border-left:1px solid var(--rule);list-style:none}
  .contact li{display:flex;align-items:center;white-space:nowrap}
  .contact svg{flex:none;fill:var(--slate)}

  /* seal band */
  .band{position:absolute;left:0;right:0;background:var(--slate)}
  .seal{position:absolute;border-radius:50%;background:var(--paper);border:2.5px solid var(--ink);box-shadow:0 0 0 3px var(--paper)}

  /* letterhead */
  .letterhead{left:45px;top:75px;width:741px;height:1042px}
  .letterhead .brand{left:72px;top:36px}
  .letterhead .brand-ring{width:76px;height:76px;margin-bottom:10px}
  .letterhead .brand-name{font-size:19px}
  .letterhead .contact{left:499px;top:51px;padding-left:16px;font-size:11.5px}
  .letterhead .contact li{height:23.5px}
  .letterhead .contact svg{width:14px;height:14px;margin-right:11px}
  .letterhead .band{top:974px;height:25px}
  .letterhead .seal{left:334px;top:951px;width:70px;height:70px}

  /* business card front */
  .card-front{left:704px;top:225px;width:410px;height:239px}
  .card-front .brand{left:18px;top:76px;width:150px}
  .card-front .brand-ring{width:54px;height:54px;margin-bottom:8px}
  .card-front .brand-name{font-size:13px}
  .card-front .divider{left:194px;top:34px;width:1px;height:143px;background:var(--rule)}
  .card-front .person{left:206px;top:30px}
  .person-name{font-size:17.5px;font-weight:600;color:var(--ink);line-height:1.3}
  .person-role{font-size:12.5px;color:var(--text)}
  .card-front .contact{left:206px;top:95px;border-left:none;font-size:11.5px}
  .card-front .contact li{height:22px}
  .card-front .contact svg{width:14px;height:14px;margin-right:12px}
  .card-front .band{top:212px;height:11px}
  .card-front .seal{left:182px;top:201px;width:32px;height:32px}

  /* business card back */
  .card-back{left:704px;top:488px;width:410px;height:239px;background:var(--slate)}
  .card-back .brand{left:105px;top:78px;width:200px}
  .card-back .brand-ring{width:58px;height:58px;border-color:var(--paper);margin-bottom:10px}
  .card-back .brand-name{color:var(--paper);font-size:12px}

  /* envelope */
  .envelope{left:600px;top:744px;width:570px;height:346px;background:transparent}
  .envelope .flap{left:0;top:0;width:570px;height:77px}
  .envelope .body{left:0;top:76px;width:570px;height:270px;background:var(--paper)}
  .envelope .brand{left:16px;top:76px;width:130px}
  .envelope .brand-ring{width:46px;height:46px;margin-bottom:7px}
  .envelope .brand-name{font-size:11px}
  .envelope .contact{left:421px;top:102px;padding-left:12px;font-size:8px}
  .envelope .contact li{height:14.5px}
  .envelope .contact svg{width:9px;height:9px;margin-right:8px}
  .envelope .band{top:318px;height:16px}
  .envelope .seal{left:264px;top:303px;width:36px;height:36px}
</style>
</head>
<body>

<svg class="sprite" aria-hidden="true">
  <defs>
    <symbol id="ico-pin" viewBox="0 0 16 16"><rect width="16" height="16"/><path d="M8 3a3 3 0 0 0-3 3c0 2.3 3 6 3 6s3-3.7 3-6a3 3 0 0 0-3-3zm0 4.2A1.2 1.2 0 1 1 8 4.8a1.2 1.2 0 0 1 0 2.4z" fill="#fff"/></symbol>
    <symbol id="ico-phone" viewBox="0 0 16 16"><rect width="16" height="16"/><path d="M3 6c0-1.5 2.2-2.5 5-2.5S13 4.5 13 6v1h-2.5V6H5.5v1H3zm2 2h6l1 4H4z" fill="#fff"/></symbol>
    <symbol id="ico-mail" viewBox="0 0 16 16"><rect width="16" height="16"/><path d="M3 5h10v6H3zm1 .8V10h8V5.8L8 8.5z" fill="#fff"/></symbol>
    <symbol id="ico-web" viewBox="0 0 16 16"><rect width="16" height="16"/><circle cx="8" cy="8" r="4.5" fill="none" stroke="#fff" stroke-width="1"/><path d="M3.5 8h9M8 3.5c-2 2.5-2 6.5 0 9M8 3.5c2 2.5 2 6.5 0 9" fill="none" stroke="#fff" stroke-width=".8"/></symbol>
  </defs>
</svg>

<!-- Letterhead -->
<section class="piece letterhead">
  <div class="brand">
    <div class="brand-ring"></div>
    <div class="brand-name">Harborline<br>Realty</div>
  </div>
  <ul class="contact">
    <li><svg><use href="#ico-pin"/></svg>Harborline Realty</li>
    <li><svg><use href="#ico-phone"/></svg>555-014-2290</li>
    <li><svg><use href="#ico-mail"/></svg>info@harborline-realty.com</li>
    <li><svg><use href="#ico-web"/></svg>www.harborline-realty.com</li>
  </ul>
  <div class="band"></div>
  <div class="seal"></div>
</section>

<!-- Business card front -->
<section class="piece card-front">
  <div class="brand">
    <div class="brand-ring"></div>
    <div class="brand-name">Harborline<br>Realty</div>
  </div>
  <div class="abs divider"></div>
  <div class="abs person">
    <div class="person-name">Daniel Reyes</div>
    <div class="person-role">Realtor</div>
  </div>
  <ul class="contact">
    <li><svg><use href="#ico-pin"/></svg>Harborline Realty</li>
    <li><svg><use href="#ico-phone"/></svg>555-014-2290</li>
    <li><svg><use href="#ico-mail"/></svg>info@harborline-realty.com</li>
    <li><svg><use href="#ico-web"/></svg>www.harborline-realty.com</li>
  </ul>
  <div class="band"></div>
  <div class="seal"></div>
</section>

<!-- Business card back -->
<section class="piece card-back">
  <div class="brand">
    <div class="brand-ring"></div>
    <div class="brand-name">Harborline Realty</div>
  </div>
</section>

<!-- Envelope -->
<section class="piece envelope">
  <svg class="abs flap" viewBox="0 0 570 77" aria-hidden="true">
    <path d="M40 0H530Q540 0 545 10L570 77H0L25 10Q30 0 40 0Z" fill="var(--slate)"/>
  </svg>
  <div class="abs body"></div>
  <div class="brand">
    <div class="brand-ring"></div>
    <div class="brand-name">Harborline<br>Realty</div>
  </div>
  <ul class="contact">
    <li><svg><use href="#ico-pin"/></svg>Harborline Realty</li>
    <li><svg><use href="#ico-phone"/></svg>555-014-2290</li>
    <li><svg><use href="#ico-mail"/></svg>info@harborline-realty.com</li>
    <li><svg><use href="#ico-web"/></svg>www.harborline-realty.com</li>
  </ul>
  <div class="band"></div>
  <div class="seal"></div>
</section>

</body>
</html>
```